Moxy Fen needs some awesome stationary

Do you have what it takes to get my brand? You either do or you don't, have a crack at a design and you my just win my business.

I don't want to waste your or my time, so put your creative genius on either a business card or envelope.

I however need a package of stationary that follows the same brand. I will message you to complete the remaining should I like your first submission.

Here is what I need, have a go!

Basically I need the following for my small business based in melbourne.
- Letterhead (printer ready and MS Word)
- Business Card
- Compliments Slip
- Envelope
- Proposal Cover Page (MS Word only)
- Presentation Folder
- Marbled Fox Cards
- Student Name Tent
- Index Cards
- Vell-Ka

I am establishing the brand and it must be modern, professional but also relaxed; that is not formal and not corporate. It represents a company are leaders, but small enough to care and operate like a bunch of friends. We are bringing people and conversations back to business, and turfing out all the bureaucracy and crazy and wasteful procedures. Its about "lets talk and figure it out together and find even better ways".

Target Market(s)

Mainly companies that build software products, but Agile practices are used in many other industries (even graphic design projects)

Industry/Entity Type

Information Technology

Font styles to use
Sans Serif

Colors
3176b5
aaaaaa

Requirements
Must have
• I like curves and circles and not boxes or rectangles.
• I want a colour rich design with my brand colours, but it must be balanced.
• I want more modern than traditional, but simple modern
Should not have
• Not corporate
• Please don't waste my time if your not going to think about it.
• Don't mess with my primary logo
• Don't change my colours
• Don't overlay logo on image

```html
<!DOCTYPE html>
<html lang="en">
<head>
<meta charset="utf-8">
<title>Moxy Fen – Index Cards</title>
<link rel="stylesheet" href="https://fonts.googleapis.com/css2?family=Open+Sans:wght@600&family=Oswald:wght@600&display=swap">
<style>
  :root {
    --bg: #39a0db;
    --paper: #ffffff;
    --rule: #2d4a9a;
    --brand: #1f4f9c;
    --shadow: rgba(20, 60, 100, 0.45);
    --tab-pink: #f7abae;
    --tab-sky: #8fd9f8;
    --tab-ice: #dff1fb;
    --tab-mint: #9cd4b0;
    --tab-lemon: #fef89d;
  }
  * { box-sizing: border-box; margin: 0; padding: 0; }
  html, body { width: 1200px; height: 960px; overflow: hidden; }
  body { background: var(--bg); position: relative; }

  .index-card {
    position: absolute;
    width: 346px;
    height: 410px;
    background: var(--paper);
    box-shadow: 5px 5px 6px var(--shadow);
    overflow: hidden;
  }
  .index-card--pink  { left: 47px;  top: 40px;  --tab: var(--tab-pink); }
  .index-card--sky   { left: 428px; top: 40px;  --tab: var(--tab-sky); }
  .index-card--ice   { left: 811px; top: 40px;  --tab: var(--tab-ice); }
  .index-card--mint  { left: 175px; top: 506px; --tab: var(--tab-mint); }
  .index-card--lemon { left: 676px; top: 510px; width: 343px; height: 408px; --tab: var(--tab-lemon); }

  .card-tab {
    position: absolute; left: 0; top: 0; width: 100%; height: 58px;
    background: var(--tab);
  }
  .card-rules {
    position: absolute; left: 0; top: 94px; width: 100%; height: 237px;
    background-image: repeating-linear-gradient(to bottom, var(--rule) 0 1px, transparent 1px 33.7px);
  }
  .card-stamp {
    position: absolute; left: 257px; top: 327px;
    width: 79px; height: 79px;
    border: 1px solid var(--rule); border-radius: 50%;
    background: var(--paper);
  }
  .index-card--lemon .card-stamp { left: 255px; }

  .brand-mark {
    position: absolute; left: 35px; top: 340px;
    width: 48px; display: flex; flex-direction: column; align-items: center;
  }
  .brand-dot {
    width: 34px; height: 34px; border-radius: 50%;
    background: var(--brand);
  }
  .brand-name {
    margin-top: 6px; white-space: nowrap;
    font: 600 15px/1 "Open Sans", sans-serif;
    color: var(--brand);
  }
  .company-name {
    position: absolute; left: 125px; top: 380px;
    font: 600 13.5px/1 "Oswald", sans-serif;
    color: var(--brand); letter-spacing: 0.2px;
  }
</style>
</head>
<body>
  <section class="index-card index-card--pink">
    <div class="card-tab"></div><div class="card-rules"></div>
    <div class="brand-mark"><span class="brand-dot"></span><span class="brand-name">Moxy Fen</span></div>
    <p class="company-name">Moxy Fen Pty Ltd</p>
    <div class="card-stamp"></div>
  </section>
  <section class="index-card index-card--sky">
    <div class="card-tab"></div><div class="card-rules"></div>
    <div class="brand-mark"><span class="brand-dot"></span><span class="brand-name">Moxy Fen</span></div>
    <p class="company-name">Moxy Fen Pty Ltd</p>
    <div class="card-stamp"></div>
  </section>
  <section class="index-card index-card--ice">
    <div class="card-tab"></div><div class="card-rules"></div>
    <div class="brand-mark"><span class="brand-dot"></span><span class="brand-name">Moxy Fen</span></div>
    <p class="company-name">Moxy Fen Pty Ltd</p>
    <div class="card-stamp"></div>
  </section>
  <section class="index-card index-card--mint">
    <div class="card-tab"></div><div class="card-rules"></div>
    <div class="brand-mark"><span class="brand-dot"></span><span class="brand-name">Moxy Fen</span></div>
    <p class="company-name">Moxy Fen Pty Ltd</p>
    <div class="card-stamp"></div>
  </section>
  <section class="index-card index-card--lemon">
    <div class="card-tab"></div><div class="card-rules"></div>
    <div class="brand-mark"><span class="brand-dot"></span><span class="brand-name">Moxy Fen</span></div>
    <p class="company-name">Moxy Fen Pty Ltd</p>
    <div class="card-stamp"></div>
  </section>
</body>
</html>
```